Residential & commercial landscaping company

Updated business cards for commercial and landscaping company. We would like to keep out logo, but just need a more updated business card.

```html
<!DOCTYPE html>
<html lang="en">
<head>
<meta charset="utf-8">
<title>GreenReach Business Cards</title>
<link href="https://fonts.googleapis.com/css2?family=Open+Sans:wght@800&family=Tinos:wght@400;700&family=Arimo:wght@400;700&display=swap" rel="stylesheet">
<style>
  :root {
    --backdrop: #2b2624;
    --card: #0b0b0b;
    --green-dark: #00693a;
    --green-mid: #00a03c;
    --green-light: #5bc24c;
    --white: #ffffff;
    --rule: #8a8a8a;
  }
  html, body {
    margin: 0;
    padding: 0;
    width: 1200px;
    height: 842px;
    overflow: hidden;
    background: var(--backdrop);
  }
  .stage {
    position: relative;
    width: 1200px;
    height: 842px;
  }
  .card {
    position: absolute;
    top: 272px;
    width: 520px;
    height: 297px;
    background: var(--card);
    overflow: hidden;
    box-shadow: 0 8px 24px rgba(0,0,0,0.55);
  }
  .card--front { left: 50px; }
  .card--back { left: 630px; }

  .band {
    position: absolute;
    left: 0;
    width: 100%;
    height: 12px;
    display: flex;
  }
  .band--top { top: 0; }
  .band--bottom { bottom: 0; }
  .band span { height: 100%; }
  .band .dark { flex: 1; background: var(--green-dark); }
  .band .mid { flex: 1; background: var(--green-mid); }
  .band .light { flex: 1; background: var(--green-light); }

  .front-content {
    position: absolute;
    left: 0;
    right: 0;
    top: 48px;
    text-align: center;
  }
  .company-name {
    font-family: "Open Sans", sans-serif;
    font-weight: 800;
    font-size: 50px;
    line-height: 1;
    color: var(--white);
    letter-spacing: -1px;
    margin: 0 0 14px 20px;
  }
  .person {
    font-family: "Tinos", serif;
    color: var(--green-light);
    font-size: 21px;
    margin: 0 0 6px 0;
  }
  .person .name { font-weight: 700; }
  .person .title { font-weight: 400; }
  .rule {
    width: 110px;
    height: 1px;
    background: var(--rule);
    margin: 0 auto 10px;
  }
  .contact {
    font-family: "Arimo", sans-serif;
    font-size: 15px;
    line-height: 1.3;
    color: var(--white);
    margin: 0;
  }
  .contact .label {
    color: var(--green-light);
    font-weight: 700;
  }

  .stripes {
    position: absolute;
    width: 60px;
    height: 56px;
  }
  .stripes--left { left: 0; top: 150px; }
  .stripes--right { right: 30px; top: 36px; }

  .brand {
    position: absolute;
    left: 0;
    right: 0;
    top: 118px;
    display: flex;
    justify-content: center;
    align-items: center;
    gap: 12px;
  }
  .brand-mark {
    width: 34px;
    height: 34px;
    background: var(--green-mid);
  }
  .brand-name {
    font-family: "Open Sans", sans-serif;
    font-weight: 800;
    font-size: 44px;
    color: var(--white);
    letter-spacing: -1px;
    line-height: 1;
  }
</style>
</head>
<body>
<main class="stage">
  <section class="card card--front">
    <div class="band band--top"><span class="dark"></span><span class="mid"></span><span class="light"></span></div>
    <div class="front-content">
      <p class="company-name">GreenReach</p>
      <p class="person"><span class="name">Daniel Marsh Jr.</span> <span class="title">- Project Manager</span></p>
      <div class="rule"></div>
      <p class="contact">555-204-7736 ext.215<br>
        <span class="label">Fax:</span> 555-310-6648<br>
        <span class="label">Email:</span> dan@GreenReachLandscapes.com</p>
    </div>
    <div class="band band--bottom"><span class="dark"></span><span class="mid"></span><span class="light"></span></div>
  </section>

  <section class="card card--back">
    <svg class="stripes stripes--left" viewBox="0 0 60 56" aria-hidden="true">
      <rect x="0" y="6" width="18" height="50" fill="var(--green-light)"/>
      <rect x="20" y="6" width="18" height="50" fill="var(--green-mid)"/>
      <rect x="40" y="0" width="18" height="50" fill="var(--green-dark)"/>
    </svg>
    <div class="brand">
      <span class="brand-mark"></span>
      <span class="brand-name">GreenReach</span>
    </div>
    <svg class="stripes stripes--right" viewBox="0 0 60 56" aria-hidden="true">
      <rect x="0" y="6" width="18" height="50" fill="var(--green-dark)"/>
      <rect x="20" y="6" width="18" height="50" fill="var(--green-mid)"/>
      <rect x="40" y="0" width="18" height="50" fill="var(--green-light)"/>
    </svg>
  </section>
</main>
</body>
</html>
```